Accommodation in an Executive Apartment for rent could be a Bed and breakfast,

Currently have a website and like the overall look but it needs revamping and want to add an instant booking button, which I would do later as the unit has a channel manager. Also want to be able to post blogs, etc. Need it to be viewed well on smart phones/tablets. all information related to this unit is on the current site which is www.hollowmerestays.com.au if you would view websites similar to roomvela.com and travonix.com Must be able to be coded in Wordpress

The current design is done in Wordpress so would want this functionality in any new design.

Target Market(s)

Workers at Parliamentary triangle, Canberra. Workers at Marlow centre Deakin, Workers at Westbrook Ellis Hanley Hospital, Workers at Fernvale Hospital, Public Servants Woden, Workers in Deakin ACT

Industry/Entity Type

Accommodation

Number of Pages Required

5+ page

Font styles to use
Sans Serif

Colors
ec1f27

Requirements
Must have
• Must have a classy look about it. Less clicks through the better. Not to wordy. Hard hitting points,
Nice to have
• Would like to retain the same colour theme and look
Should not have
• anything tacky

```html
<!DOCTYPE html>
<html lang="en">
<head>
<meta charset="utf-8">
<title>Hollowmere executive bed + breakfast</title>
<link href="https://fonts.googleapis.com/css2?family=Open+Sans:wght@400;600;700&display=swap" rel="stylesheet">
<style>
:root{
  --red:#c91f26;
  --red-deep:#a3161c;
  --ink:#333333;
  --muted:#8a8a8a;
  --light:#f2f2f2;
  --dark:#1c1c1c;
  --darker:#0e0e0e;
  --white:#ffffff;
}
*{box-sizing:border-box;margin:0;padding:0}
html,body{width:1200px;height:2168px;overflow:hidden}
body{font-family:"Open Sans",Arial,sans-serif;color:var(--ink);background:var(--white);position:relative}

/* header */
.site-header{position:absolute;top:0;left:0;width:1200px;height:80px;background:var(--red);display:flex;align-items:center;justify-content:space-between;padding:0 40px 0 24px}
.brand{color:var(--white);font-size:19px;font-weight:600;display:flex;align-items:center;gap:10px}
.brand-mark{width:12px;height:12px;border-radius:50%;background:var(--white)}
.main-nav{display:flex;gap:34px}
.main-nav a{color:var(--white);font-size:11px;font-weight:600;text-decoration:none;letter-spacing:.3px;padding-bottom:6px;border-bottom:2px solid transparent}
.main-nav a.active{border-bottom-color:var(--white)}

/* hero */
.hero{position:absolute;top:80px;left:0;width:1200px;height:610px;background:linear-gradient(120deg,#3a0d0f 0%,#7a1c1f 35%,#4a1a17 60%,#2b1b18 100%)}
.hero-arrow{position:absolute;top:305px;width:30px;height:30px;border-radius:50%;background:rgba(255,255,255,.85)}
.hero-arrow.prev{left:22px}
.hero-arrow.next{right:22px}
.hero-arrow svg{position:absolute;top:8px;left:8px}
.availability{position:absolute;left:100px;top:420px;width:1000px}
.availability-tab{width:200px;height:42px;background:rgba(20,20,20,.75);color:var(--white);font-weight:700;font-size:17px;padding:9px 18px}
.availability-form{background:rgba(20,20,20,.6);padding:24px 30px;display:grid;grid-template-columns:repeat(4,1fr);gap:18px 28px}
.field{height:30px;background:var(--white);font-size:10px;color:var(--muted);padding:8px 10px;display:flex;justify-content:space-between;align-items:center}
.field::after{content:"";border:4px solid transparent;border-top-color:#999;margin-top:4px}
.booking-btn{height:30px;background:var(--red);color:var(--white);font-size:12px;font-weight:700;display:flex;align-items:center;justify-content:center;letter-spacing:.5px}

/* welcome */
.welcome{position:absolute;top:690px;left:0;width:1200px;height:410px;text-align:center}
.section-title{font-size:24px;font-weight:700;color:var(--ink);text-transform:uppercase}
.section-title span{color:var(--red)}
.welcome .section-title{margin-top:38px}
.welcome-intro{width:760px;margin:16px auto 0;font-size:10.5px;line-height:17px;color:var(--muted)}
.features{display:grid;grid-template-columns:repeat(4,250px);margin:40px 100px 0}
.feature-icon{width:82px;height:82px;border-radius:50%;background:#3a3a3a;margin:0 auto;display:flex;align-items:center;justify-content:center}
.feature-icon.accent{background:var(--red)}
.feature h3{font-size:14px;font-weight:600;margin-top:18px;color:var(--ink)}
.feature p{font-size:10px;line-height:15px;color:var(--muted);width:170px;margin:6px auto 0}

/* blog */
.blog{position:absolute;top:1100px;left:0;width:1200px;height:440px;background:var(--light)}
.blog .section-title{text-align:center;margin-top:34px;font-size:20px}
.blog-grid{display:grid;grid-template-columns:repeat(3,1fr);gap:28px;margin:30px 100px 0}
.blog-photo{height:168px}
.blog-card h4{color:var(--red);font-size:13px;font-weight:600;margin-top:14px}
.blog-card p{font-size:10px;line-height:15px;color:var(--muted);margin-top:6px}
.blog-date{font-size:10px;color:var(--muted);margin-top:10px;display:flex;align-items:center;gap:6px}

/* partners */
.partners{position:absolute;top:1540px;left:0;width:1200px;height:140px;display:flex;justify-content:space-between;align-items:center;padding:0 100px}
.partner{height:46px;background:#d9d9d9}
.partner.p1{width:140px;background:#cfd6e2}
.partner.p2{width:118px;border-radius:10px;background:#e6c9c9}
.partner.p3{width:130px;border-radius:50%;background:#d2d2d2}
.partner.p4{width:135px;background:#e2b8b8}
.partner.p5{width:140px;border-radius:6px;background:#ece0a6}

/* contact */
.contact{position:absolute;top:1680px;left:0;width:1200px;height:420px;background:linear-gradient(180deg,#1e1e1e,#141414)}
.contact .section-title{color:var(--white);text-align:center;margin-top:52px;font-size:20px}
.contact-form{position:absolute;left:100px;top:136px;width:370px}
.input{height:30px;border:1px solid rgba(255,255,255,.6);color:#ccc;font-size:10px;padding:8px 10px;margin-bottom:16px}
.input.message{height:120px}
.contact-info{position:absolute;left:500px;top:136px;width:320px;color:#ddd;font-size:11px;line-height:16px}
.contact-info li{list-style:none;display:flex;gap:12px;margin-bottom:14px}
.contact-info svg{flex:none;margin-top:2px}

/* footer */
.site-footer{position:absolute;top:2100px;left:0;width:1200px;height:68px;background:var(--darker);display:flex;justify-content:space-between;align-items:center;padding:0 100px;color:#888;font-size:10px}
.social{display:flex;gap:18px}
.social span{width:12px;height:12px;border-radius:50%;background:#aaa}
</style>
</head>
<body>

<header class="site-header">
  <div class="brand"><span class="brand-mark"></span>Hollowmere executive bed + breakfast</div>
  <nav class="main-nav">
    <a class="active">HOME</a>
    <a>B&amp;B ACCOMMODATION</a>
    <a>GALLERY</a>
    <a>WHAT'S NEARBY</a>
    <a>GUEST BOOK</a>
    <a>CONTACT US</a>
  </nav>
</header>

<section class="hero" role="img" aria-label="Dining table in the executive apartment with a red candle, wine bottle and glasses">
  <span class="hero-arrow prev"><svg width="14" height="14" viewBox="0 0 14 14"><path d="M9 2 L4 7 L9 12" stroke="#333" stroke-width="2" fill="none"/></svg></span>
  <span class="hero-arrow next"><svg width="14" height="14" viewBox="0 0 14 14"><path d="M5 2 L10 7 L5 12" stroke="#333" stroke-width="2" fill="none"/></svg></span>
  <div class="availability">
    <div class="availability-tab">Check Availability</div>
    <div class="availability-form">
      <div class="field">Select Apartment</div>
      <div class="field">Select Room</div>
      <div class="field">Adults</div>
      <div class="field">Kids</div>
      <div class="field">Arrival</div>
      <div class="field">Departure</div>
      <div class="field">Select Guest Row</div>
      <div class="booking-btn">BOOKING NOW</div>
    </div>
  </div>
</section>

<section class="welcome">
  <h2 class="section-title">Welcome to <span>Hollowmere Accommodation</span></h2>
  <p class="welcome-intro">Sed ut perspiciatis unde omnis iste natus error sit voluptatem accusantium doloremque laudantium, totam rem aperiam, eaque ipsa quae ab illo inventore veritatis et quasi architecto beatae vitae dicta sunt explicabo. Nemo enim ipsam voluptatem quia voluptas sit aspernatur aut odit aut fugit, sed quia consequuntur magni dolores eos qui ratione.</p>
  <div class="features">
    <div class="feature">
      <div class="feature-icon accent"><svg width="36" height="36" viewBox="0 0 36 36"><path d="M18 4 L21 15 L32 20 L32 23 L21 20 L20 28 L24 31 L24 33 L18 31 L12 33 L12 31 L16 28 L15 20 L4 23 L4 20 L15 15 Z" fill="#fff"/></svg></div>
      <h3>Nemo enim ipsam</h3>
      <p>Sed ut perspiciatis unde omnis iste natus error sit voluptatem doloremque laudantium totam.</p>
    </div>
    <div class="feature">
      <div class="feature-icon"><svg width="38" height="30" viewBox="0 0 38 30"><path d="M4 18 L8 8 L30 8 L34 18 L34 24 L4 24 Z" fill="#fff"/><circle cx="11" cy="24" r="4" fill="#3a3a3a" stroke="#fff" stroke-width="2"/><circle cx="27" cy="24" r="4" fill="#3a3a3a" stroke="#fff" stroke-width="2"/><rect x="11" y="11" width="16" height="6" fill="#3a3a3a"/></svg></div>
      <h3>Nemo enim ipsam</h3>
      <p>Sed ut perspiciatis unde omnis iste natus error sit voluptatem doloremque laudantium totam.</p>
    </div>
    <div class="feature">
      <div class="feature-icon"><svg width="40" height="30" viewBox="0 0 40 30"><circle cx="9" cy="20" r="7" fill="none" stroke="#fff" stroke-width="2.5"/><circle cx="31" cy="20" r="7" fill="none" stroke="#fff" stroke-width="2.5"/><path d="M9 20 L16 8 L26 8 L31 20 M16 8 L20 20 L26 8 M14 5 L19 5" fill="none" stroke="#fff" stroke-width="2.5"/></svg></div>
      <h3>Nemo enim ipsam</h3>
      <p>Sed ut perspiciatis unde omnis iste natus error sit voluptatem doloremque laudantium totam.</p>
    </div>
    <div class="feature">
      <div class="feature-icon"><svg width="34" height="34" viewBox="0 0 34 34"><circle cx="17" cy="17" r="14" fill="none" stroke="#fff" stroke-width="2.5"/><ellipse cx="17" cy="17" rx="6" ry="14" fill="none" stroke="#fff" stroke-width="2"/><path d="M3 17 H31 M6 9 H28 M6 25 H28" stroke="#fff" stroke-width="2"/></svg></div>
      <h3>Nemo enim ipsam</h3>
      <p>Sed ut perspiciatis unde omnis iste natus error sit voluptatem doloremque laudantium totam.</p>
    </div>
  </div>
</section>

<section class="blog">
  <h2 class="section-title">From our Blog</h2>
  <div class="blog-grid">
    <article class="blog-card">
      <div class="blog-photo" role="img" aria-label="Bright apartment hallway with timber floor" style="background:linear-gradient(135deg,#c9a77a,#8a6a48)"></div>
      <h4>On the other hand, we denoun...</h4>
      <p>At vero eos et accusamus et iusto odio dignissimos ducimus qui blanditiis praesentium voluptatum [...]</p>
      <div class="blog-date"><svg width="10" height="10" viewBox="0 0 10 10"><rect x="1" y="2" width="8" height="7" fill="none" stroke="#999"/><path d="M1 4 H9" stroke="#999"/></svg>19 Nov 2015</div>
    </article>
    <article class="blog-card">
      <div class="blog-photo" role="img" aria-label="Living room with red cushions and sofa" style="background:linear-gradient(135deg,#d8c7b4,#9a3a32)"></div>
      <h4>On the other hand, we denoun...</h4>
      <p>At vero eos et accusamus et iusto odio dignissimos ducimus qui blanditiis praesentium voluptatum [...]</p>
      <div class="blog-date"><svg width="10" height="10" viewBox="0 0 10 10"><rect x="1" y="2" width="8" height="7" fill="none" stroke="#999"/><path d="M1 4 H9" stroke="#999"/></svg>19 Nov 2015</div>
    </article>
    <article class="blog-card">
      <div class="blog-photo" role="img" aria-label="Front entrance of the apartment with garden" style="background:linear-gradient(135deg,#9fb07a,#5e6b4a)"></div>
      <h4>On the other hand, we denoun...</h4>
      <p>At vero eos et accusamus et iusto odio dignissimos ducimus qui blanditiis praesentium voluptatum [...]</p>
      <div class="blog-date"><svg width="10" height="10" viewBox="0 0 10 10"><rect x="1" y="2" width="8" height="7" fill="none" stroke="#999"/><path d="M1 4 H9" stroke="#999"/></svg>19 Nov 2015</div>
    </article>
  </div>
</section>

<section class="partners" aria-label="Partners">
  <div class="partner p1"></div>
  <div class="partner p2"></div>
  <div class="partner p3"></div>
  <div class="partner p4"></div>
  <div class="partner p5"></div>
</section>

<section class="contact" role="img" aria-label="Darkened apartment interior behind the contact form">
  <h2 class="section-title">Contact us now !</h2>
  <div class="contact-form">
    <div class="input">Name</div>
    <div class="input">Email</div>
    <div class="input message">Message</div>
  </div>
  <ul class="contact-info">
    <li><svg width="10" height="14" viewBox="0 0 10 14"><path d="M5 0 C2 0 0 2 0 5 C0 9 5 14 5 14 C5 14 10 9 10 5 C10 2 8 0 5 0 Z" fill="#ddd"/><circle cx="5" cy="5" r="2" fill="#1c1c1c"/></svg>On the other hand, we denounce with righteous indignation and dislike men</li>
    <li><svg width="12" height="10" viewBox="0 0 12 10"><rect x=".5" y=".5" width="11" height="9" fill="none" stroke="#ddd"/><path d="M.5 .5 L6 5 L11.5 .5" fill="none" stroke="#ddd"/></svg>stay@hollowmerestays.com.au</li>
    <li><svg width="12" height="12" viewBox="0 0 12 12"><path d="M2 0 L5 3 L3.5 5 C4.5 7 5 7.5 7 8.5 L9 7 L12 10 L10 12 C5 12 0 7 0 2 Z" fill="#ddd"/></svg>02 6100 4827</li>
  </ul>
</section>

<footer class="site-footer">
  <div>© 2015 Hollowmere accommodation . All rights reserved</div>
  <div class="social"><span></span><span></span><span></span><span></span><span></span><span></span></div>
</footer>

</body>
</html>
```